Law Offices business card

Hi there, I'll need business card for the Law Offices of Colin Matheny. The information must convey his strategic approach and quick resolution to complex business litigation needs. Please emphasize Civil Litigation, Corporate Law, Business Governance and Real Estate Law. Colin has over 25 years of experience in these fields.The card should be modern and edgy and the message should be clear. Please consult his current website for ideas.

```html
<!DOCTYPE html>
<html lang="en">
<head>
<meta charset="utf-8">
<title>Law Offices of Colin Matheny – Business Card</title>
<link href="https://fonts.googleapis.com/css2?family=Tinos:wght@400&family=Arimo:wght@400&display=swap" rel="stylesheet">
<style>
  :root {
    --stage: #e6e3de;
    --card-black: #0b0b0b;
    --card-black-hi: #1c1c1c;
    --ink-white: #ffffff;
    --ink-soft: #e9e9e9;
    --paper: #ffffff;
    --paper-shade: #e4e4e4;
    --ink-dark: #1a1a1a;
    --art-light: #f2efe8;
    --art-mid: #c9c2b2;
    --art-dark: #6d6558;
  }
  * { margin: 0; padding: 0; box-sizing: border-box; }
  html, body { width: 1200px; height: 892px; overflow: hidden; }
  body {
    background: var(--stage);
    display: flex;
    align-items: center;
    justify-content: center;
    gap: 40px;
  }
  .card {
    width: 540px;
    height: 309px;
    position: relative;
    overflow: hidden;
    box-shadow: 0 10px 28px rgba(0,0,0,.25);
  }

  /* Front */
  .card-front {
    background: linear-gradient(160deg, var(--card-black-hi) 0%, var(--card-black) 55%);
    color: var(--ink-white);
  }
  .firm-name {
    position: absolute;
    left: 30px; top: 26px;
    font: 400 30px/1 "Tinos", "Times New Roman", serif;
    letter-spacing: .2px;
  }
  .person {
    position: absolute;
    left: 90px; top: 88px;
    font-family: "Tinos", "Times New Roman", serif;
  }
  .person-name { font-size: 34px; line-height: 1; }
  .person-title { font-size: 22px; line-height: 1.1; margin-top: 2px; }
  .rule {
    position: absolute;
    left: 88px; top: 146px;
    width: 1px; height: 146px;
    background: var(--ink-soft);
  }
  .contacts {
    position: absolute;
    left: 100px; top: 156px;
    list-style: none;
    font: 400 18px/1 "Arimo", Arial, sans-serif;
  }
  .contacts li {
    display: flex;
    align-items: center;
    gap: 14px;
    height: 26px;
  }
  .icon {
    width: 17px; height: 17px;
    background: var(--ink-white);
    border-radius: 2px;
    display: flex; align-items: center; justify-content: center;
    flex: none;
  }
  .icon svg { width: 13px; height: 13px; }

  /* Back */
  .card-back {
    background: linear-gradient(120deg, var(--paper) 0%, var(--paper) 40%, var(--paper-shade) 100%);
    color: var(--ink-dark);
  }
  .services-heading {
    position: absolute;
    left: 32px; top: 28px;
    font: 400 40px/1 "Tinos", "Times New Roman", serif;
  }
  .services {
    position: absolute;
    left: 34px; top: 88px;
    list-style: none;
    font: 400 18px/1.55 "Arimo", Arial, sans-serif;
    z-index: 1;
  }
  .legal-art {
    position: absolute;
    right: 0; bottom: 0;
    width: 330px; height: 240px;
    background: radial-gradient(ellipse at 55% 55%, var(--art-light) 0%, var(--art-mid) 60%, rgba(201,194,178,0) 100%);
    opacity: .8;
  }
</style>
</head>
<body>

  <section class="card card-front" aria-label="Business card front">
    <h1 class="firm-name">Law Offices of Colin Matheny, P.A.</h1>
    <div class="person">
      <p class="person-name">Colin Matheny</p>
      <p class="person-title">Attorney</p>
    </div>
    <span class="rule"></span>
    <ul class="contacts">
      <li>
        <span class="icon"><svg viewBox="0 0 16 16"><path d="M3 2h3l1 3-2 1.5a8 8 0 0 0 4.5 4.5L11 9l3 1v3a1 1 0 0 1-1 1A11 11 0 0 1 2 3a1 1 0 0 1 1-1z" fill="#000"/></svg></span>
        561-555-0147
      </li>
      <li>
        <span class="icon"><svg viewBox="0 0 16 16"><rect x="4.5" y="1" width="7" height="14" rx="1.2" fill="#000"/><rect x="5.8" y="3" width="4.4" height="8" fill="#fff"/></svg></span>
        561-555-0183
      </li>
      <li>
        <span class="icon"><svg viewBox="0 0 16 16"><rect x="1.5" y="3.5" width="13" height="9" fill="none" stroke="#000" stroke-width="1.4"/><path d="M1.5 3.5 8 9l6.5-5.5" fill="none" stroke="#000" stroke-width="1.4"/></svg></span>
        colin@mathenylaw.com
      </li>
      <li>
        <span class="icon"><svg viewBox="0 0 16 16"><circle cx="8" cy="8" r="6.3" fill="none" stroke="#000" stroke-width="1.3"/><ellipse cx="8" cy="8" rx="2.8" ry="6.3" fill="none" stroke="#000" stroke-width="1.1"/><path d="M1.7 8h12.6" stroke="#000" stroke-width="1.1"/></svg></span>
        www.mathenylaw.com
      </li>
      <li>
        <span class="icon"><svg viewBox="0 0 16 16"><path d="M8 15s5-5.2 5-8.7A5 5 0 0 0 3 6.3C3 9.8 8 15 8 15z" fill="#000"/><circle cx="8" cy="6.3" r="1.8" fill="#fff"/></svg></span>
        118B Harbor Lane, Palm Beach, Florida 33480
      </li>
    </ul>
  </section>

  <section class="card card-back" aria-label="Business card back">
    <div class="legal-art" role="img" aria-label="Soft illustration of legal objects: scales of justice, gavel, law books and a graduation cap"></div>
    <h2 class="services-heading">Services :</h2>
    <ul class="services">
      <li>Civil Litigation</li>
      <li>Corporate Law</li>
      <li>Business Governance and Real Estate Law</li>
    </ul>
  </section>

</body>
</html>
```